PlayTallyCollective - Game Statistics and Achievement Tracking

I need a new modern design for an existing website.

The website is a project to track statistics and achievements for games (currently Vaporn Achievements/Stats and stats for Cargo Haul Odyssey 2 and Frontier Rig Journeys).
I am currently expanding the site with other platforms (like QVR) and more games.
I am also adding a user registration/signin with user profiles to show off their achievements and stats across all platforms and games.

The current website is available at https://plytly.example/
To search for data you can use the username "pixelornin" (without quotes).

The design should be modern and extendable and contain space for a logo.

The logo should match the project. It should combine Gaming with statistics.

Target Market(s)

Video game players

Number of Pages Required

5+ page

Font styles to use
Sans Serif

Requirements
Must have
• Basic Layout, User profile page (not yet available on live site), Search Page for Platforms/Games, Platform profile page, Dark theme

```html
<!DOCTYPE html>
<html lang="en">
<head>
<meta charset="utf-8">
<title>PlayTallyCollective – Game Statistics and Achievements</title>
<link href="https://fonts.googleapis.com/css2?family=Audiowide&family=Lato:wght@400;700&display=swap" rel="stylesheet">
<style>
:root{
  --bg:#0a0e1c;
  --bg-2:#111729;
  --panel:#15192a;
  --panel-2:#1b2033;
  --blue:#2a3ff0;
  --blue-2:#3d55ff;
  --white:#ffffff;
  --muted:#c8ccd8;
  --line:#3a3f55;
  --red:#b2404d;
  --indigo:#3f4bb0;
}
*{box-sizing:border-box;margin:0;padding:0}
html,body{width:1200px;height:3406px;overflow:hidden}
body{background:linear-gradient(180deg,#0a0d18 0,#0d1224 900px,#0c1122 1700px,#0b0f1e 2200px,#090c17 3406px);color:var(--white);font-family:'Lato',sans-serif;position:relative}
.abs{position:absolute}
.display{font-family:'Audiowide',sans-serif}

/* header */
.hero-scene{left:0;top:0;width:1200px;height:700px;background:radial-gradient(ellipse at 55% 70%,#2b3448 0,#1a2030 35%,#0c111d 70%),linear-gradient(180deg,#141a28,#0b0f1b);}
.hero-scene::after{content:"";position:absolute;inset:0;background:linear-gradient(180deg,rgba(10,13,24,.75) 0,rgba(10,13,24,.2) 30%,rgba(10,13,24,.3) 70%,#0b0f1c 100%)}
.nav a{position:absolute;top:44px;font-size:15px;color:var(--white);text-decoration:none}
.nav a.active{color:var(--blue-2);text-decoration:underline}
.brand{left:450px;top:30px;width:300px;text-align:center}
.brand .mark{width:64px;height:64px;border-radius:14px;background:var(--white);margin:0 auto 14px}
.brand .name{font-family:'Audiowide',sans-serif;font-size:20px;color:var(--white)}
.hero-title{left:0;width:1200px;top:245px;text-align:center;font-size:58px}
.hero-sub{left:250px;width:700px;top:340px;text-align:center;font-size:23px;line-height:34px}
.btn{display:block;background:var(--blue);color:var(--white);border-radius:20px;text-align:center;font-size:15px;line-height:38px;height:38px;width:154px;text-decoration:none}
.dots{left:568px;top:597px}
.dots span{display:inline-block;width:18px;height:6px;border-radius:3px;background:var(--white);margin-right:4px}
.dots span:first-child{background:var(--blue-2)}

/* carousel */
.band{top:733px;height:235px;width:120px;background:var(--blue)}
.band.l{left:0;clip-path:polygon(0 0,100% 8%,100% 92%,0 100%)}
.band.r{right:0;clip-path:polygon(0 8%,100% 0,100% 100%,0 92%)}
.arrow{width:40px;height:40px;border-radius:50%;background:var(--white);display:flex;align-items:center;justify-content:center}
.game{background:var(--panel);border-radius:6px;overflow:hidden;text-align:center;box-shadow:0 10px 30px rgba(0,0,0,.5)}
.game .art{position:relative;width:100%}
.game .pill{position:absolute;left:50%;bottom:-8px;transform:translateX(-50%);background:var(--blue);border-radius:10px;font-size:10px;padding:3px 10px;white-space:nowrap}
.game h3{font-size:15px;margin-top:18px;white-space:nowrap}
.game p{font-size:10px;line-height:12px;margin:6px 6px 0;color:var(--muted)}
.game.main h3{font-size:19px;margin-top:30px}
.game.main p{font-size:12px}
.game.main .pill{font-size:12px;padding:4px 16px}

/* search */
.search-bar{left:111px;top:1097px;width:978px;height:86px;background:var(--panel);border-radius:4px}
.field{border:1px solid var(--line);border-radius:3px;height:43px;font-size:13px;display:flex;align-items:center;padding-left:16px}
.sq-btn{width:29px;height:27px;background:#5a5e6e;border-radius:2px;display:flex;align-items:center;justify-content:center}

/* profile */
.profile{left:111px;top:1267px;width:978px;height:430px;border:1.5px solid var(--white);border-radius:14px;background:rgba(10,13,28,.8)}
.avatar{left:155px;top:1323px;width:279px;height:273px;border:3px solid var(--white);background:linear-gradient(135deg,#5e8ed9,#c59a5a 55%,#3a4c8a)}
.stat-label{left:514px;font-size:20px;font-weight:700}
.stat-icon{left:694px}
.stat-value{left:740px;font-size:16px}
.chip{top:1628px;height:32px;width:46px;font-size:16px;text-align:center;line-height:32px}

/* sections */
.section-title{left:0;width:1200px;text-align:center;font-size:44px}
.section-title em{font-style:normal;color:var(--blue-2)}
.stat-card{top:1858px;width:306px;height:274px;background:var(--panel-2);text-align:center}
.stat-card.grid{background:linear-gradient(180deg,#141a3c,#2a2150 55%,#3b2350)}
.stat-card .num{font-family:'Audiowide',sans-serif;font-size:44px;margin-top:14px}
.stat-card .lbl{font-size:26px;margin-top:8px}
.user-card{width:480px;height:145px;background:var(--panel-2);border-radius:3px}
.user-card .photo{position:absolute;left:13px;top:9px;width:137px;height:128px}
.user-card h4{position:absolute;left:187px;top:18px;font-family:'Audiowide',sans-serif;font-size:17px;color:var(--blue-2);font-weight:400}
.user-card p{position:absolute;left:186px;top:52px;width:260px;font-size:15px;line-height:22px}
.user-card a{position:absolute;left:187px;top:104px;font-family:'Audiowide',sans-serif;font-size:15px;color:var(--blue-2);text-decoration:none}

/* footer */
.foot-brand{left:300px;width:600px;top:2945px;text-align:center}
.foot-brand .mark{width:180px;height:180px;border-radius:36px;background:var(--white);margin:0 auto 30px}
.foot-brand .name{font-family:'Audiowide',sans-serif;font-size:46px;line-height:56px}
.foot-nav{left:0;width:1200px;top:3281px;text-align:center;font-size:15px}
.foot-nav a{color:var(--white);text-decoration:none;margin:0 24px}
.foot-nav a.active{color:var(--blue-2);text-decoration:underline}
.foot-nav span{color:var(--white)}
.rule{left:111px;top:3362px;width:978px;height:1px;background:var(--line)}
.copy{left:0;width:1200px;top:3380px;text-align:center;font-size:15px}
</style>
</head>
<body>

<div class="abs hero-scene" role="img" aria-label="Night-time city street scene with lit buildings and traffic"></div>

<nav class="nav">
  <a class="active" href="#" style="left:184px">Home</a>
  <a href="#" style="left:273px">About Us</a>
  <a href="#" style="left:383px">Users</a>
  <a href="#" style="left:735px">Games</a>
  <a href="#" style="left:830px">Statistics</a>
  <a href="#" style="left:939px">Contact Us</a>
</nav>

<div class="abs brand"><div class="mark"></div><div class="name">PlayTallyCollective</div></div>

<h1 class="abs hero-title display">PlayTallyCollective</h1>
<p class="abs hero-sub">We offer you free and easy insights into your game statistics and achievements on multiple platforms and games.</p>
<a class="abs btn" href="#" style="left:523px;top:432px">Register Now</a>
<div class="abs dots"><span></span><span></span><span></span></div>

<!-- game carousel -->
<div class="abs band l"></div>
<div class="abs band r"></div>

<div class="abs game" style="left:114px;top:714px;width:110px;height:239px">
  <div class="art" style="height:170px;background:linear-gradient(180deg,#1c2233,#3b8f3a 50%,#1c2233)" role="img" aria-label="Sprout Trail Quest cover art"><span class="pill">More Details</span></div>
  <h3>Sprout Trail</h3><p>Partial controller support</p>
</div>
<div class="abs game" style="left:222px;top:704px;width:122px;height:268px">
  <div class="art" style="height:192px;background:linear-gradient(160deg,#9fe06a,#6fc4d8 60%,#c9a060)" role="img" aria-label="Tiny Realm cover art"><span class="pill">More Details</span></div>
  <h3>Tiny Realm</h3><p>Complete the fisher quest</p>
</div>
<div class="abs game" style="left:341px;top:688px;width:146px;height:304px">
  <div class="art" style="height:220px;background:linear-gradient(180deg,#1a2030,#5a2a3c 50%,#1a2030)" role="img" aria-label="Breakout 2190 cover art"><span class="pill">More Details</span></div>
  <h3>Breakout 2190</h3><p>You didn't think it would be this easy, did you</p>
</div>
<div class="abs game" style="left:710px;top:688px;width:147px;height:304px">
  <div class="art" style="height:220px;background:linear-gradient(180deg,#3a2418,#8a2a1c 45%,#111)" role="img" aria-label="Exit the Chamber cover art"><span class="pill">More Details</span></div>
  <h3>Exit the Chamber</h3><p>Allowed to leave. In the end I was alone!</p>
</div>
<div class="abs game" style="left:857px;top:704px;width:122px;height:268px">
  <div class="art" style="height:192px;background:linear-gradient(180deg,#1a2030,#4a6ad8 50%,#c04ab0 70%,#1a2030)" role="img" aria-label="GridMind cover art"><span class="pill">More Details</span></div>
  <h3>GridMind</h3><p>Solved without undo or retry</p>
</div>
<div class="abs game" style="left:979px;top:714px;width:106px;height:239px">
  <div class="art" style="height:170px;background:linear-gradient(180deg,#1c2233,#2a1a1a 50%,#1c2233)" role="img" aria-label="Dread Manor 2 Demo cover art"><span class="pill">More Details</span></div>
  <h3>Manor 2 Demo</h3><p>Free to leave. In the end I was alone!</p>
</div>
<div class="abs game main" style="left:483px;top:667px;width:229px;height:345px">
  <div class="art" style="height:248px;background:linear-gradient(180deg,#9a7ab8,#d89ab8 45%,#6a5a9a 80%,#c7a0c0)" role="img" aria-label="Toward the Stars cover art"><span class="pill">More Details</span></div>
  <h3>Toward the Stars</h3><p>Send the pilot to the stars.</p>
</div>

<div class="abs arrow" style="left:57px;top:817px"><svg width="16" height="16" viewBox="0 0 16 16"><path d="M10 2 4 8l6 6" fill="none" stroke="#0a0e1c" stroke-width="2.5"/></svg></div>
<div class="abs arrow" style="left:1103px;top:817px"><svg width="16" height="16" viewBox="0 0 16 16"><path d="M6 2l6 6-6 6" fill="none" stroke="#0a0e1c" stroke-width="2.5"/></svg></div>

<!-- search -->
<div class="abs search-bar"></div>
<div class="abs field" style="left:133px;top:1118px;width:524px">Search Game</div>
<div class="abs" style="left:600px;top:1118px;width:57px;height:43px;border-left:1px solid var(--line);display:flex;align-items:center;justify-content:center">
  <svg width="20" height="20" viewBox="0 0 20 20"><circle cx="8" cy="8" r="6" fill="none" stroke="#fff" stroke-width="2"/><path d="M12.5 12.5 18 18" stroke="#fff" stroke-width="2"/></svg>
</div>
<div class="abs field" style="left:666px;top:1118px;width:309px;justify-content:space-between;padding-right:20px">Achievement Progress
  <svg width="14" height="10" viewBox="0 0 14 10"><path d="M2 2l5 5 5-5" fill="none" stroke="#fff" stroke-width="2"/></svg>
</div>
<div class="abs sq-btn" style="left:997px;top:1126px"><svg width="14" height="12" viewBox="0 0 14 12"><path d="M1 2h12M3 6h8M5 10h4" stroke="#ddd" stroke-width="1.6"/></svg></div>
<div class="abs sq-btn" style="left:1037px;top:1126px"><svg width="14" height="14" viewBox="0 0 14 14"><path d="M1 1h12L8 7v6L6 12V7z" fill="none" stroke="#ddd" stroke-width="1.4"/></svg></div>

<!-- profile -->
<section class="abs profile"></section>
<div class="abs" style="left:161px;top:1285px;font-size:17px">pixelornin</div>
<svg class="abs" style="left:1030px;top:1286px" width="22" height="22" viewBox="0 0 22 22"><circle cx="9" cy="9" r="7" fill="none" stroke="#fff" stroke-width="2"/><path d="M14 14l6 6" stroke="#fff" stroke-width="2"/></svg>
<div class="abs avatar" role="img" aria-label="User avatar illustration"></div>

<div class="abs stat-label" style="top:1319px">Played Games:</div>
<div class="abs stat-label" style="top:1371px">Total play time:</div>
<div class="abs stat-label" style="top:1422px">Achievements:</div>
<div class="abs stat-label" style="top:1474px">Member since:</div>
<div class="abs stat-label" style="top:1525px">Last played:</div>
<div class="abs stat-label" style="top:1577px">Last Update:</div>

<svg class="abs stat-icon" style="top:1322px" width="24" height="24" viewBox="0 0 24 24"><path d="M3 6h2M8 6h13M3 12h2M8 12h13M3 18h2M8 18h13" stroke="#fff" stroke-width="1.8"/></svg>
<svg class="abs stat-icon" style="top:1370px" width="24" height="24" viewBox="0 0 24 24"><circle cx="12" cy="12" r="9" fill="none" stroke="#fff" stroke-width="1.8"/><path d="M12 7v5h4" fill="none" stroke="#fff" stroke-width="1.8"/></svg>
<svg class="abs stat-icon" style="top:1423px" width="24" height="24" viewBox="0 0 24 24"><path d="M3 6h18v4a2 2 0 0 0 0 4v4H3v-4a2 2 0 0 0 0-4z" fill="none" stroke="#fff" stroke-width="1.8"/></svg>
<svg class="abs stat-icon" style="top:1473px" width="24" height="24" viewBox="0 0 24 24"><rect x="4" y="5" width="16" height="16" rx="2" fill="none" stroke="#fff" stroke-width="1.8"/><path d="M4 10h16M8 3v4M16 3v4" stroke="#fff" stroke-width="1.8"/></svg>
<div class="abs" style="left:697px;top:1522px;width:20px;height:20px;background:#e0284a;border-radius:3px"></div>
<svg class="abs stat-icon" style="top:1574px" width="24" height="24" viewBox="0 0 24 24"><path d="M6 8a8 8 0 1 0 6-3" fill="none" stroke="#fff" stroke-width="1.8"/><path d="M12 2v6l-4-3z" fill="#fff"/></svg>

<div class="abs stat-value" style="top:1321px">1166 / 1644 (70%)</div>
<div class="abs stat-value" style="top:1373px">1 year 2 months 11 hours 25 minutes</div>
<div class="abs stat-value" style="top:1424px;left:744px">18007 / 63070 (28%)</div>
<div class="abs stat-value" style="top:1476px">14.01.2009</div>
<div class="abs stat-value" style="top:1527px">Rail Conductor® 5</div>
<div class="abs stat-value" style="top:1579px">26.12.2024 12:53h</div>

<div class="abs chip" style="left:155px;background:var(--blue)">179</div>
<div class="abs chip" style="left:215px;background:var(--indigo)">15</div>
<div class="abs chip" style="left:275px;background:var(--red)">87</div>
<svg class="abs" style="left:345px;top:1632px" width="36" height="24" viewBox="0 0 36 24"><rect width="36" height="8" fill="#000"/><rect y="8" width="36" height="8" fill="#dd0000"/><rect y="16" width="36" height="8" fill="#ffce00"/></svg>

<svg class="abs" style="left:929px;top:1653px" width="22" height="22" viewBox="0 0 24 24"><path d="M6 8a8 8 0 1 0 6-3" fill="none" stroke="#fff" stroke-width="1.8"/><path d="M12 2v6l-4-3z" fill="#fff"/></svg>
<svg class="abs" style="left:966px;top:1653px" width="22" height="22" viewBox="0 0 24 24"><rect x="4" y="5" width="16" height="16" rx="2" fill="none" stroke="#fff" stroke-width="1.8"/><path d="M4 10h16M8 3v4M16 3v4" stroke="#fff" stroke-width="1.8"/></svg>
<div class="abs" style="left:1005px;top:1654px;width:20px;height:20px;border-radius:50%;background:#fff"></div>
<svg class="abs" style="left:1042px;top:1653px" width="22" height="22" viewBox="0 0 24 24"><ellipse cx="12" cy="5" rx="8" ry="3" fill="none" stroke="#fff" stroke-width="1.8"/><path d="M4 5v14c0 1.7 3.6 3 8 3s8-1.3 8-3V5M4 10c0 1.7 3.6 3 8 3s8-1.3 8-3M4 15c0 1.7 3.6 3 8 3s8-1.3 8-3" fill="none" stroke="#fff" stroke-width="1.8"/></svg>

<!-- user statistics -->
<h2 class="abs section-title display" style="top:1770px">User <em>Statistics</em></h2>

<div class="abs stat-card" style="left:111px">
  <svg style="margin-top:58px" width="70" height="50" viewBox="0 0 70 50"><path d="M14 4h42c8 0 12 8 14 22s-2 22-8 22c-5 0-8-6-12-10H20c-4 4-7 10-12 10S-2 40 0 26 6 4 14 4z" fill="var(--blue-2)"/><path d="M17 16v16M9 24h16" stroke="#15192a" stroke-width="5"/><circle cx="48" cy="19" r="3.5" fill="#15192a"/><circle cx="56" cy="27" r="3.5" fill="#15192a"/><circle cx="40" cy="27" r="3.5" fill="#15192a"/><circle cx="48" cy="34" r="3.5" fill="#15192a"/></svg>
  <div class="num">251966</div><div class="lbl">Games</div>
</div>
<div class="abs stat-card grid" style="left:446px" role="img" aria-label="Achievements count on a neon grid backdrop">
  <svg style="margin-top:50px" width="64" height="64" viewBox="0 0 64 64"><path d="M16 4h32v18c0 10-7 18-16 18S16 32 16 22z" fill="var(--blue-2)"/><path d="M16 10H6c0 10 4 16 12 18M48 10h10c0 10-4 16-12 18" fill="none" stroke="var(--blue-2)" stroke-width="5"/><rect x="28" y="40" width="8" height="10" fill="var(--blue-2)"/><rect x="18" y="50" width="28" height="8" rx="2" fill="var(--blue-2)"/></svg>
  <div class="num">2692707</div><div class="lbl">Game Achievements</div>
</div>
<div class="abs stat-card" style="left:782px">
  <svg style="margin-top:52px" width="66" height="62" viewBox="0 0 66 62"><rect x="4" y="40" width="10" height="20" fill="var(--blue-2)"/><rect x="18" y="32" width="10" height="28" fill="var(--blue-2)"/><rect x="32" y="38" width="10" height="22" fill="var(--blue-2)"/><rect x="46" y="22" width="10" height="38" fill="var(--blue-2)"/><path d="M4 30l16-12 12 8L58 6" fill="none" stroke="var(--blue-2)" stroke-width="4"/><path d="M50 4h12v12z" fill="var(--blue-2)"/></svg>
  <div class="num">339284</div><div class="lbl">Game Stats</div>
</div>
<div class="abs arrow" style="left:57px;top:1976px"><svg width="16" height="16" viewBox="0 0 16 16"><path d="M10 2 4 8l6 6" fill="none" stroke="#0a0e1c" stroke-width="2.5"/></svg></div>
<div class="abs arrow" style="left:1103px;top:1976px"><svg width="16" height="16" viewBox="0 0 16 16"><path d="M6 2l6 6-6 6" fill="none" stroke="#0a0e1c" stroke-width="2.5"/></svg></div>

<!-- our users -->
<h2 class="abs section-title display" style="top:2206px">Our <em>Users</em></h2>

<article class="abs user-card" style="left:111px;top:2293px"><div class="photo" style="background:linear-gradient(135deg,#7a2a6a,#2a3a8a)" role="img" aria-label="Photo of an excited gamer"></div><h4>Lorem Ipsum</h4><p>Risus commodo viverra maecenas accumsan lacus vel facilisis.</p><a href="#">Read More ...</a></article>
<article class="abs user-card" style="left:607px;top:2293px"><div class="photo" style="background:linear-gradient(135deg,#1a2a4a,#3a6a9a)" role="img" aria-label="Photo of a gamer with headphones"></div><h4>Lorem Ipsum</h4><p>Risus commodo viverra maecenas accumsan lacus vel facilisis.</p><a href="#">Read More ...</a></article>
<article class="abs user-card" style="left:111px;top:2463px"><div class="photo" style="background:linear-gradient(135deg,#e8e8ea,#c8442a 70%)" role="img" aria-label="Photo of a gamer holding a controller"></div><h4>Lorem Ipsum</h4><p>Risus commodo viverra maecenas accumsan lacus vel facilisis.</p><a href="#">Read More ...</a></article>
<article class="abs user-card" style="left:607px;top:2463px"><div class="photo" style="background:linear-gradient(135deg,#0a1a3a,#e07a2a)" role="img" aria-label="Photo of a focused gamer in warm light"></div><h4>Lorem Ipsum</h4><p>Risus commodo viverra maecenas accumsan lacus vel facilisis.</p><a href="#">Read More ...</a></article>
<article class="abs user-card" style="left:111px;top:2634px"><div class="photo" style="background:linear-gradient(135deg,#c83a8a,#2a4ab0 60%,#1a2a6a)" role="img" aria-label="Photo of a gamer at a neon-lit desk"></div><h4>Lorem Ipsum</h4><p>Risus commodo viverra maecenas accumsan lacus vel facilisis.</p><a href="#">Read More ...</a></article>
<article class="abs user-card" style="left:607px;top:2634px"><div class="photo" style="background:linear-gradient(135deg,#8a2ab0,#1a2a4a 60%,#3a6ac8)" role="img" aria-label="Photo of a gamer facing several monitors"></div><h4>Lorem Ipsum</h4><p>Risus commodo viverra maecenas accumsan lacus vel facilisis.</p><a href="#">Read More ...</a></article>

<a class="abs btn" href="#" style="left:523px;top:2817px">View All</a>

<!-- footer -->
<div class="abs foot-brand"><div class="mark"></div><div class="name">PlayTallyCollective</div></div>

<nav class="abs foot-nav">
  <a class="active" href="#">Home</a><span>|</span><a href="#">About Us</a><span>|</span><a href="#">Users</a><span>|</span><a href="#">Games</a><span>|</span><a href="#">Statistics</a><span>|</span><a href="#">Contact Us</a>
</nav>
<div class="abs rule"></div>
<p class="abs copy">Copyright © 2024 PlayTallyCollective. All rights reserved.</p>

</body>
</html>
```